Business cards for Norwegian software consultancy business

We are in need of business cards for our Norwegian consultancy company.
“Valto Brindex AS” specializes in software development, architecture and agile methodology, providing mostly on-site services at customers.
The cards should reflect a certain level of business professionalism with an elegant touch, while paying tribute to our modern and technological heritage. Our logo should be featured, as well as room for basic information about the cardholder and legal information of the company (company name, address and VAT number).
We would like our cards to reflect that we are a modern consulting company. It should present a professional image that people will remember. The texture and color pallette should reflect our professionalism and reliability, so we prefer a light color pallette with colors such as gray, white, blue and black. The number of colors used should however not be overwhelming, with the text being distinct and readable.
We are open to untraditional layouts and playful designs as long as they communicate the intent stated above.
You could also take a look at our website http://www.brindex.no for input on our visual profile.
Our logo is attached in the form of vectors and rasterized PNG. Please comment if you would like the black-white and/or inverted versions as well.
Industry/Entity Type
Architecture
Contact Information for Business Card
Company information:
Valto Brindex AS
Kvernlia 14, 3170 Sem
482 71 519
info@brindex.no
www.brindex.no
Employee information:
Full name
Title
Email
Phone
Font styles to use
Look and feel

```html
<!DOCTYPE html>
<html lang="en">
<head>
<meta charset="utf-8">
<title>Valto Brindex AS – Business Cards</title>
<link href="https://fonts.googleapis.com/css2?family=Lato:wght@400;700&display=swap" rel="stylesheet">
<style>
  :root {
    --backdrop: #cfcdcb;
    --brand-blue: #5389b3;
    --ink: #222423;
    --paper: #f6f6f5;
    --white: #ffffff;
    --muted-white: #e6eef5;
  }
  * { box-sizing: border-box; margin: 0; padding: 0; }
  html, body {
    width: 1200px; height: 900px; overflow: hidden;
    background: var(--backdrop);
    font-family: "Lato", Arial, sans-serif;
  }
  .sheet { position: relative; width: 1200px; height: 900px; }

  .card {
    position: absolute; left: 325px;
    width: 550px; height: 314px;
    box-shadow: 0 6px 18px rgba(0,0,0,.18);
    overflow: hidden;
  }
  .card--front { top: 70px; background: var(--brand-blue); }
  .card--back  { top: 480px; background: var(--paper); }

  .wordmark {
    position: absolute; left: 0; right: 0;
    display: flex; align-items: center; justify-content: center; gap: 14px;
  }
  .wordmark__square { width: 22px; height: 22px; }
  .wordmark__name {
    font-weight: 400; font-size: 34px; letter-spacing: 3px;
  }
  .card--front .wordmark { top: 130px; }
  .card--front .wordmark__square { background: var(--white); }
  .card--front .wordmark__name { color: var(--white); }
  .card--back .wordmark { top: 46px; }
  .card--back .wordmark__square { background: var(--brand-blue); }
  .card--back .wordmark__name { color: var(--ink); }

  .holder {
    position: absolute; left: 0; top: 168px;
    width: 290px; height: 100px;
    background: var(--brand-blue); color: var(--white);
    display: flex; flex-direction: column; align-items: center; justify-content: center;
  }
  .holder::before {
    content: ""; position: absolute; top: -9px; left: 130px;
    border-left: 9px solid transparent; border-right: 9px solid transparent;
    border-bottom: 9px solid var(--brand-blue);
  }
  .holder__name { font-size: 19px; font-weight: 400; }
  .holder__title { font-size: 11px; letter-spacing: .5px; text-transform: uppercase; margin-top: 2px; }

  .contact {
    position: absolute; left: 296px; top: 126px;
    width: 254px; height: 142px;
    background: var(--ink); color: var(--white);
    padding: 34px 0 0 60px;
    list-style: none;
  }
  .contact::before {
    content: ""; position: absolute; left: -1px; top: 80px;
    border-top: 8px solid transparent; border-bottom: 8px solid transparent;
    border-left: 8px solid var(--paper);
  }
  .contact__item { display: flex; align-items: center; gap: 12px; font-size: 13.5px; line-height: 18px; }
  .contact__item svg { width: 11px; height: 11px; fill: var(--white); flex: none; }

  .legal {
    position: absolute; left: 0; right: 0; bottom: 14px;
    text-align: center; font-size: 13px; color: var(--ink); font-weight: 700;
  }
  .legal__company { color: var(--brand-blue); }
</style>
</head>
<body>
<main class="sheet">
  <section class="card card--front" aria-label="Card front">
    <div class="wordmark">
      <span class="wordmark__square"></span>
      <span class="wordmark__name">VALTO BRINDEX</span>
    </div>
  </section>

  <section class="card card--back" aria-label="Card back">
    <div class="wordmark">
      <span class="wordmark__square"></span>
      <span class="wordmark__name">VALTO BRINDEX</span>
    </div>

    <div class="holder">
      <span class="holder__name">Henrik Solberg</span>
      <span class="holder__title">Director</span>
    </div>

    <ul class="contact">
      <li class="contact__item">
        <svg viewBox="0 0 12 12" aria-hidden="true"><path d="M2 1l2 0 1 3-1.3 1a7 7 0 0 0 3.3 3.3L8 7l3 1v2a1 1 0 0 1-1 1A9 9 0 0 1 1 2a1 1 0 0 1 1-1z"/></svg>
        482 71 519
      </li>
      <li class="contact__item">
        <svg viewBox="0 0 12 12" aria-hidden="true"><rect x="3" y="1" width="6" height="3"/><rect x="1" y="5" width="10" height="4" rx="1"/><rect x="3" y="8" width="6" height="3"/></svg>
        482 71 520
      </li>
      <li class="contact__item">
        <svg viewBox="0 0 12 12" aria-hidden="true"><path d="M1 2h10v8H1z M2 3v.3l4 3 4-3V3z" fill-rule="evenodd"/></svg>
        hsolberg@brindex.no
      </li>
      <li class="contact__item">
        <svg viewBox="0 0 12 12" aria-hidden="true"><circle cx="6" cy="6" r="5"/></svg>
        www.brindex.no
      </li>
    </ul>

    <p class="legal"><span>Valto </span><span class="legal__company">Brindex AS</span><span>, Kvernlia 14, 3170 Sem</span></p>
  </section>
</main>
</body>
</html>
```